KRWB new business card design

We need a business card design for our established business which is Australia wide however based in Melbourne. We are a young team of Financial Planners who specialize in Insurance and Basic super advice for people like us.

We are people who help our clients get things done in a timely and cost effective manner whilst having a good time and a laugh along the way.

We would like this to have a consistent feel with our new e-brochure which i have attached from a color and font perspective.

Industry/Entity Type

Business

Requirements
Must have
• We do not need specific address details rather just the states we are in:

VIC/NSW/QLD/TAS
Nice to have
• Curved edge to mate the brochure

```html
<!DOCTYPE html>
<html lang="en">
<head>
<meta charset="utf-8">
<title>KRWB business card</title>
<link href="https://fonts.googleapis.com/css2?family=Jost:ital,wght@0,400;0,600;1,400&display=swap" rel="stylesheet">
<style>
  :root {
    --stage: #2b2b2b;
    --card: #ffffff;
    --green-light: #8dc63f;
    --green-deep: #77a83a;
    --green-dark: #00a651;
    --ink: #222222;
    --grey: #555555;
  }
  * { box-sizing: border-box; margin: 0; padding: 0; }
  html, body {
    width: 1200px; height: 900px; overflow: hidden;
    background: var(--stage);
    font-family: "Jost", "Futura", sans-serif;
  }
  .canvas { position: relative; width: 1200px; height: 900px; }
  .card {
    position: absolute; top: 105px; width: 413px; height: 667px;
    background: var(--card); overflow: hidden;
  }
  .card--front { left: 172px; border-bottom-right-radius: 80px; }
  .card--back { left: 666px; width: 411px; border-bottom-left-radius: 80px; }

  .brand { position: absolute; display: flex; align-items: center; gap: 10px; }
  .brand__square { background: var(--green-light); }
  .brand__name { font-weight: 600; color: var(--grey); letter-spacing: 1px; line-height: 1; }
  .card--front .brand { left: 31px; top: 340px; }
  .card--front .brand__square { width: 34px; height: 34px; }
  .card--front .brand__name { font-size: 40px; }

  .contact { position: absolute; left: 31px; top: 424px; color: var(--ink); }
  .contact__name { font-size: 15px; font-weight: 600; color: var(--green-light); letter-spacing: 1px; line-height: 1.1; }
  .contact__role { font-size: 12px; font-weight: 600; color: var(--green-light); letter-spacing: 1px; margin-bottom: 6px; }
  .contact__legal { font-size: 11px; font-style: italic; line-height: 12px; margin-bottom: 7px; }
  .contact__phones { font-size: 12.5px; line-height: 13px; letter-spacing: 1px; }
  .contact__label { display: inline-block; width: 18px; color: var(--green-light); }
  .contact__web { font-size: 12.5px; line-height: 14px; letter-spacing: 1px; }

  .card--back .brand { left: 138px; top: 270px; }
  .card--back .brand__square { width: 40px; height: 40px; }
  .card--back .brand__name { font-size: 50px; }

  .services { position: absolute; left: 138px; top: 365px; color: var(--ink); font-size: 13px; line-height: 16px; letter-spacing: 0.5px; list-style: none; }
  .services__title { margin-bottom: 1px; }

  .curve-panel {
    position: absolute; left: 138px; top: 467px; width: 136px; height: 200px;
    border-radius: 68px 68px 0 0;
    background: linear-gradient(160deg, var(--green-light), var(--green-deep));
  }
</style>
</head>
<body>
<main class="canvas">
  <section class="card card--front" aria-label="Card front">
    <div class="brand">
      <span class="brand__square"></span>
      <span class="brand__name">KRWB</span>
    </div>
    <div class="contact">
      <p class="contact__name">Daniel Marsh</p>
      <p class="contact__role">Financial Adviser</p>
      <p class="contact__legal">Kindred Wealth Partners Pty Ltd<br>Authorised Representatives<br>Meridian Advice Group Limited<br>Australian Financial Services Licensee</p>
      <p class="contact__phones">
        <span class="contact__label">p</span>1300 555 214<br>
        <span class="contact__label">f</span>03 9555 0187<br>
        <span class="contact__label">m</span>0412 555 946
      </p>
      <p class="contact__web">NSW VIC TAS QLD<br>daniel@krwb.com.au<br>www.krwb.com.au</p>
    </div>
  </section>

  <section class="card card--back" aria-label="Card back">
    <div class="brand">
      <span class="brand__square"></span>
      <span class="brand__name">KRWB</span>
    </div>
    <ul class="services">
      <li class="services__title">Specialising in:</li>
      <li>Risk Insurance</li>
      <li>Debt Management</li>
      <li>Superannuation</li>
      <li>Wealth Creation</li>
      <li>Retirement Planning</li>
    </ul>
    <div class="curve-panel"></div>
  </section>
</main>
</body>
</html>
```